Church needs a street sign design

We're a small church located in Silicon Valley, California. Our website is https://www.vgtmarlowfield.org/ and our address is 4817 Ferrow Ave, San Jose, California, 95873. You can look up our location on Google Maps to see the sign from Street View. I have uploaded an image of the street sign as well. The marquee, the top section of the sign, and the separating line between them both will be removed. We're seeking a design for a new backlit acrylic insert that will go on the front of the light box and the back of the lightbox. The acrylic sign will fill the entire external frame. In the future, we may build a decorative wood frame around the structural legs, as visualized in one of the uploaded files. The church's brand colors are: #003366 (dark blue), #ff6600 (vibrant orange), #228b22 (forest green). I have also uploaded the church's logo assets. Our primary font is Montserrat and the secondary is Poppins. You can deviate from these colors/fonts if the sign is still coherent with the rest of our branding. Our branding values are mission, truth, passion, and community (please do not put those words on the sign! They are just intended to guide the look of the design). The sign dimensions are 96" by 47.5". Keep in mind that the sign will be backlit on a busy street side. It will also be positioned next to an old-looking church building. We do NOT want a sign that looks traditional, old, or antiquated. Instead, we want a modern-looking sign that pairs well with our old building while helping it look more modern too. We would also like the web address clearly visible on the sign: vgtmarlowfield.org. If you have any questions, just let me know!

```html
<!DOCTYPE html>
<html lang="en">
<head>
<meta charset="utf-8">
<title>Valley Gate Tabernacle – Street Sign Insert</title>
<link rel="stylesheet" href="https://fonts.googleapis.com/css2?family=Montserrat:wght@500&family=Poppins:wght@600;700;800&family=Yellowtail&display=swap">
<style>
  :root {
    --stage: #a3a3a3;
    --navy: #003366;
    --navy-deep: #00234a;
    --orange: #ff6600;
    --white: #ffffff;
    --ink: #1c0b0b;
    --url-light: #e6e8ee;
    --sky-light: #f6c07a;
    --sky-mid: #b86a3c;
    --hill-dark: #0b0604;
  }
  html, body {
    margin: 0;
    width: 1200px;
    height: 888px;
    overflow: hidden;
    background: var(--stage);
  }
  .sign {
    position: absolute;
    left: 40px;
    top: 167px;
    width: 1120px;
    height: 553px;
    display: block;
  }
  .headline {
    font-family: "Poppins", sans-serif;
    font-weight: 800;
    fill: var(--navy);
    letter-spacing: -1px;
  }
  .tagline-script {
    font-family: "Yellowtail", cursive;
    fill: var(--white);
  }
  .tagline-glory {
    font-family: "Poppins", sans-serif;
    font-weight: 700;
    fill: var(--ink);
  }
  .web-address {
    font-family: "Poppins", sans-serif;
    font-weight: 600;
    letter-spacing: 2px;
  }
  .web-address .web-muted { fill: var(--url-light); }
  .web-address .web-name { fill: var(--orange); }
  .church-name {
    font-family: "Montserrat", sans-serif;
    font-weight: 500;
    fill: var(--white);
  }
</style>
</head>
<body>
<svg class="sign" viewBox="0 0 1120 553" xmlns="http://www.w3.org/2000/svg" aria-label="Church street sign">
  <defs>
    <linearGradient id="sunset" x1="0" y1="0" x2="0.25" y2="1">
      <stop offset="0" stop-color="var(--sky-light)"/>
      <stop offset="0.3" stop-color="var(--sky-mid)"/>
      <stop offset="0.55" stop-color="#4a2417"/>
      <stop offset="0.75" stop-color="var(--hill-dark)"/>
      <stop offset="1" stop-color="#000"/>
    </linearGradient>
  </defs>

  <!-- sunrise photo area -->
  <rect class="photo-area" x="0" y="0" width="1120" height="553" fill="url(#sunset)"
        role="img" aria-label="Photo of a cross silhouetted on a hilltop at sunrise"/>

  <!-- torn white panel -->
  <polygon class="message-panel" fill="var(--white)"
    points="750,0 1120,0 1120,420 400,420 420,390 438,382 452,352 470,344 488,310 505,300 522,268 540,258 560,226 575,214 596,196 614,170 634,156 650,126 668,114 686,86 700,74 718,42 734,30"/>

  <!-- navy base band -->
  <polygon class="address-band" fill="var(--navy-deep)"
    points="408,398 440,393 470,397 520,389 560,395 600,388 650,393 700,387 760,394 810,390 860,384 905,391 950,388 1000,392 1050,389 1090,393 1110,386 1120,382 1120,553 257,553 275,530 292,520 310,490 330,476 350,448 370,436 388,412"/>

  <!-- headline -->
  <text class="headline" x="1053" y="123" text-anchor="end" font-size="82">MAKING</text>
  <text class="headline" x="1053" y="191" text-anchor="end" font-size="82">DISCIPLES</text>

  <!-- brush band -->
  <polygon class="brush-band" fill="var(--orange)"
    points="440,221 500,216 560,218 620,212 700,214 780,211 860,213 940,210 1010,212 1070,215 1062,226 1075,236 1060,246 1072,258 1058,268 1068,280 1000,283 930,280 860,284 780,281 700,283 620,280 560,283 500,279 462,276 482,268 446,262 470,254 438,246 474,238 448,230 476,226"/>
  <text class="tagline-script" x="758" y="262" text-anchor="middle" font-size="54">&amp; Helping the Helpless</text>

  <text class="tagline-glory" x="1053" y="347" text-anchor="end" font-size="44" textLength="552" lengthAdjust="spacingAndGlyphs">FOR THE GLORY OF CHRIST</text>

  <!-- web address -->
  <text class="web-address" x="1050" y="490" text-anchor="end" font-size="52" textLength="690" lengthAdjust="spacingAndGlyphs"><tspan class="web-muted">www.</tspan><tspan class="web-name">vgtmarlowfield</tspan><tspan class="web-muted">.org</tspan></text>

  <!-- church name -->
  <rect class="name-mark" x="64" y="404" width="46" height="46" fill="none" stroke="var(--white)" stroke-width="4"/>
  <text class="church-name" x="126" y="433" font-size="32">VALLEY GATE</text>
  <text class="church-name" x="127" y="452" font-size="13.5" letter-spacing="1">TABERNACLE</text>
</svg>
</body>
</html>
```